DJ Colm Vetter

I'm looking for a professional but still artsy/progressive design. I come from a hip hop/club DJ background playing a lot of underground music but have switched to doing more corporate parties and weddings recently. I am all about keeping the dancefloor moving and emotionally connecting with the crowd. I'd like a trendy/updated color palette. Something that's clean enough that looks professional but also trendy enough to convey that by the end of the night we'll be sweatily dancing to the latest hits. Some designers/artists I like: Tarn Olquist, Pavel Remy, Wendell Quarrie, Lumeno 7400, Silas Dravin.

```html
<!DOCTYPE html>
<html lang="en">
<head>
<meta charset="utf-8">
<title>DJ Colm Vetter – Business Card</title>
<link rel="stylesheet" href="https://fonts.googleapis.com/css2?family=Roboto+Slab:wght@300;400&display=swap">
<style>
  :root {
    --page-bg: #2b241d;
    --card-black: #07090f;
    --photo-deep: #0b0f1c;
    --photo-mid: #1b2340;
    --photo-glow: #2b3766;
    --accent-cyan: #3ec4f2;
    --text-white: #f2f4f7;
  }
  html, body {
    margin: 0;
    padding: 0;
    width: 1200px;
    height: 1023px;
    overflow: hidden;
    background: var(--page-bg);
  }
  .stage {
    position: relative;
    width: 1200px;
    height: 1023px;
    display: flex;
    align-items: center;
    justify-content: center;
  }
  .business-card {
    position: relative;
    width: 900px;
    height: 514px;
    border-radius: 28px;
    overflow: hidden;
    background: var(--card-black);
    box-shadow: 0 24px 60px rgba(0,0,0,0.55);
  }
  .dj-photo {
    position: absolute;
    inset: 0;
    background:
      radial-gradient(ellipse 45% 55% at 55% 38%, var(--photo-glow) 0%, transparent 70%),
      radial-gradient(ellipse 40% 45% at 78% 75%, var(--photo-mid) 0%, transparent 75%),
      linear-gradient(160deg, var(--photo-mid) 0%, var(--photo-deep) 55%, var(--card-black) 100%);
  }
  .card-info {
    position: absolute;
    left: 64px;
    top: 250px;
    display: flex;
    align-items: center;
    gap: 26px;
  }
  .dj-name {
    margin: 0;
    font-family: "Roboto Slab", serif;
    font-weight: 400;
    font-size: 40px;
    letter-spacing: 0.5px;
    text-transform: uppercase;
    color: var(--accent-cyan);
    white-space: nowrap;
  }
  .divider {
    width: 2px;
    height: 120px;
    background: var(--accent-cyan);
  }
  .contact-list {
    list-style: none;
    margin: 0;
    padding: 0;
    font-family: "Roboto Slab", serif;
    font-weight: 300;
    font-size: 27px;
    line-height: 1.45;
    color: var(--text-white);
  }
  .contact-label {
    color: var(--accent-cyan);
    font-weight: 400;
  }
</style>
</head>
<body>
  <main class="stage">
    <article class="business-card">
      <div class="dj-photo" role="img" aria-label="Photo of the DJ wearing headphones, smiling and mixing at turntables in a dark club"></div>
      <div class="card-info">
        <h1 class="dj-name">DJ Colm Vetter</h1>
        <span class="divider"></span>
        <ul class="contact-list">
          <li><span class="contact-label">P:</span> +330 5817-4402</li>
          <li><span class="contact-label">E:</span> info@DJColmVetter.com</li>
          <li><span class="contact-label">W:</span> nightbloomsessions.com</li>
        </ul>
      </div>
    </article>
  </main>
</body>
</html>
```